Volbrey Inc Business Card

Looking to get an updated business card for a Contract Machining company (www.volbreyinc.example) - looking for a clean design the portrays the technical nature of the business - colors can follow the website design and be in any combination that makes sense (red black, white, metallic or silver) - logos attached for use also. Would like space for: Name, title, business phone (555 214-3086), cell phone , website (www.volbreyinc.example) - possibly QR code could be integrated for website (designer choice), business address - 418 Harlow Bend, Ashvale, NR 48199 (cards will be for 4 employees, I will either need to modify a template or I can provide individual information)
Target Market(s)
Aerospace, defense and medical device manufacturing companies that need machining
Industry/Entity Type
Machining for aerospace, defense, medical
Contact Information for Business Card
Name, Title, Business Phone, Cell Phone, email, business website and business address
Look and feel

```html
<!DOCTYPE html>
<html lang="en">
<head>
<meta charset="utf-8">
<title>Volbrey Inc Business Card</title>
<link href="https://fonts.googleapis.com/css2?family=Montserrat:wght@400;500;700;800&display=swap" rel="stylesheet">
<style>
  :root {
    --brand-red: #b21e24;
    --card-white: #ffffff;
    --ink: #1d1d1d;
    --stage: #e9e6e2;
  }
  * { margin: 0; padding: 0; box-sizing: border-box; }
  html, body { width: 1200px; height: 931px; overflow: hidden; }
  body {
    background: var(--stage);
    font-family: "Montserrat", sans-serif;
    position: relative;
  }
  .card {
    position: absolute;
    width: 620px;
    height: 354px;
    background: var(--card-white);
    border-radius: 18px;
    overflow: hidden;
    box-shadow: 0 10px 28px rgba(0,0,0,0.18);
  }
  .card::after {
    content: "";
    position: absolute;
    left: 0; right: 0; bottom: 0;
    height: 16px;
    background: var(--brand-red);
  }
  .card-front { left: 60px; top: 70px; }
  .card-back { left: 520px; top: 500px; }

  .front-mark {
    position: absolute;
    left: 50%; top: 50%;
    transform: translate(-50%, -54%);
    display: flex; flex-direction: column; align-items: center; gap: 14px;
  }
  .mark-circle {
    border-radius: 50%;
    background: var(--brand-red);
  }
  .front-mark .mark-circle { width: 190px; height: 190px; }
  .brand-name {
    color: var(--brand-red);
    font-weight: 800;
    letter-spacing: 1px;
    text-transform: uppercase;
    white-space: nowrap;
  }
  .front-mark .brand-name { font-size: 30px; }

  .back-mark .mark-circle {
    position: absolute;
    right: 44px; top: 28px;
    width: 124px; height: 124px;
  }
  .back-mark .brand-name {
    position: absolute;
    right: 30px; top: 158px;
    font-size: 30px;
  }
  .rule {
    position: absolute;
    left: 40px; right: 30px; top: 206px;
    height: 1.5px;
    background: var(--brand-red);
  }
  .person-name {
    position: absolute;
    left: 40px; top: 168px;
    font-size: 26px; font-weight: 700;
    color: var(--brand-red);
    white-space: nowrap;
  }
  .person-title {
    position: absolute;
    left: 48px; top: 212px;
    font-size: 15px; color: var(--ink);
  }
  .contact-list {
    position: absolute;
    left: 48px; top: 240px;
    list-style: none;
  }
  .contact-list li {
    display: flex; align-items: center; gap: 10px;
    font-size: 15px; color: var(--ink);
    height: 22px;
    white-space: nowrap;
  }
  .contact-list svg { width: 14px; height: 14px; fill: var(--brand-red); flex: none; }
  .address {
    position: absolute;
    right: 30px; top: 278px;
    text-align: right;
    font-size: 14px; line-height: 20px; color: var(--ink);
    font-style: normal;
    white-space: nowrap;
  }
</style>
</head>
<body>
  <section class="card card-front" aria-label="Card front">
    <div class="front-mark">
      <div class="mark-circle"></div>
      <div class="brand-name">Volbrey</div>
    </div>
  </section>

  <section class="card card-back" aria-label="Card back">
    <div class="back-mark">
      <div class="mark-circle"></div>
      <div class="brand-name">Volbrey</div>
    </div>
    <div class="person-name">Daren Holt</div>
    <div class="rule"></div>
    <div class="person-title">Owner</div>
    <ul class="contact-list">
      <li><svg viewBox="0 0 24 24"><path d="M6.6 10.8a15 15 0 0 0 6.6 6.6l2.2-2.2c.3-.3.7-.4 1-.2 1.1.4 2.3.6 3.6.6.6 0 1 .4 1 1V20c0 .6-.4 1-1 1C10.6 21 3 13.4 3 4c0-.6.4-1 1-1h3.5c.6 0 1 .4 1 1 0 1.3.2 2.5.6 3.6.1.3 0 .7-.2 1z"/></svg>555 214-3086</li>
      <li><svg viewBox="0 0 24 24"><path d="M3 8c0-2 4-4 9-4s9 2 9 4v2h-5V8H8v2H3zM6 11h12l2 9H4zm6 2.5a2.5 2.5 0 1 0 0 5 2.5 2.5 0 0 0 0-5z"/></svg>555 214-3086</li>
      <li><svg viewBox="0 0 24 24"><path d="M2 5h20v14H2zm2 2v.5l8 5 8-5V7zm0 2.8V17h16V9.8l-8 5z"/></svg>info@volbreyinc.example</li>
      <li><svg viewBox="0 0 24 24"><path d="M12 2a10 10 0 1 0 0 20 10 10 0 0 0 0-20zm-1 17.9A8 8 0 0 1 4.2 10L9 14.8v1.2a2 2 0 0 0 2 2zm6.9-2.5A2 2 0 0 0 16 16h-1v-3a1 1 0 0 0-1-1H8v-2h2a1 1 0 0 0 1-1V7h2a2 2 0 0 0 2-2v-.4a8 8 0 0 1 2.9 12.8z"/></svg>www.volbreyinc.example</li>
    </ul>
    <address class="address">
      418 Harlow Bend,<br>Ashvale, NR 48199
    </address>
  </section>
</body>
</html>
```